Web Developer Needs a Business Card Design

I need a personal business card design that represents me as a web developer for potential employers. I would like the background to be a dark color on the front for contrast with my logo and name. The back will have all my information along with a smaller version of the logo. I want something with a modern look and feel, not too conservative. This will be used for potential employers and freelance work.

Industry/Entity Type

Business

Contact Information for Business Card

Front should have my logo and name. The back should have all my personal information which would include: name: Tom Varulek, phone: 570-614-3098, email: tomvarulek@quillbox.net, website url: www.tomvarulek.net, logo, web developer.

Font styles to use
Sans Serif

Requirements
Must have
• Must include my logo. The color palette base color will be the logo color.

```html
<!DOCTYPE html>
<html lang="en">
<head>
<meta charset="utf-8">
<title>Tom Varulek – Business Card</title>
<link rel="stylesheet" href="https://fonts.googleapis.com/css2?family=Arimo:wght@400;700&display=swap">
<style>
  :root {
    --page-bg: #e9e6e1;
    --card-black: #0b0b0b;
    --brand-teal: #6cc3b0;
    --card-white: #f4f4f4;
    --ink: #111111;
    --wordmark-grey: #d6d6d6;
  }
  * { margin: 0; padding: 0; box-sizing: border-box; }
  html, body {
    width: 1200px;
    height: 902px;
    overflow: hidden;
    background: var(--page-bg);
    font-family: "Arimo", Arial, sans-serif;
  }
  .sheet {
    width: 1200px;
    height: 902px;
    display: flex;
    align-items: center;
    justify-content: center;
    gap: 40px;
  }
  .card {
    width: 540px;
    height: 309px;
    box-shadow: 0 10px 28px rgba(0, 0, 0, 0.22);
  }
  .card svg { display: block; }
  .front-wordmark { font-family: "Arimo", Arial, sans-serif; font-weight: 700; fill: var(--wordmark-grey); letter-spacing: 5px; }
  .holder-name { font-family: "Arimo", Arial, sans-serif; font-weight: 400; fill: var(--ink); }
  .holder-title { font-family: "Arimo", Arial, sans-serif; font-weight: 700; fill: var(--ink); }
  .contact-line { font-family: "Arimo", Arial, sans-serif; font-weight: 400; fill: var(--ink); }
</style>
</head>
<body>
<main class="sheet">

  <section class="card card-front" aria-label="Card front">
    <svg width="540" height="309" viewBox="0 0 540 309">
      <rect class="front-bg" width="540" height="309" fill="var(--card-black)"/>
      <circle class="brand-ring" cx="270" cy="128" r="92" fill="none" stroke="var(--brand-teal)" stroke-width="12" role="img" aria-label="Logo position"/>
      <text class="front-wordmark" x="270" y="272" font-size="30" text-anchor="middle">TOM VARULEK</text>
    </svg>
  </section>

  <section class="card card-back" aria-label="Card back">
    <svg width="540" height="309" viewBox="0 0 540 309">
      <rect class="back-bg" width="540" height="309" fill="var(--brand-teal)"/>
      <path class="side-band-edge" d="M0 0 H200 Q290 150 196 309 H0 Z" fill="var(--card-white)"/>
      <path class="side-band" d="M0 0 H188 Q276 150 184 309 H0 Z" fill="var(--card-black)"/>

      <circle class="brand-ring" cx="108" cy="196" r="76" fill="none" stroke="var(--brand-teal)" stroke-width="10" role="img" aria-label="Logo position"/>

      <text class="holder-name" x="508" y="66" font-size="36" text-anchor="end">Tom Varulek</text>
      <text class="holder-title" x="508" y="96" font-size="22" text-anchor="end">Web Developer</text>

      <g class="contact-list">
        <text class="contact-line" x="494" y="196" font-size="16" text-anchor="end">570-614-3098</text>
        <text class="contact-line" x="494" y="226" font-size="16" text-anchor="end">tomvarulek@quillbox.net</text>
        <text class="contact-line" x="494" y="256" font-size="16" text-anchor="end">www.tomvarulek.net</text>

        <g class="icon icon-phone">
          <rect x="502" y="182" width="17" height="17" rx="2" fill="var(--ink)"/>
          <path d="M506 188 q4.5 -3 9 0 v2 h-2.5 v-1 h-4 v1 h-2.5 Z M507 191 h7 v4 h-7 Z" fill="var(--card-white)"/>
        </g>
        <g class="icon icon-mail">
          <rect x="502" y="212" width="17" height="17" rx="2" fill="var(--ink)"/>
          <rect x="505" y="216.5" width="11" height="8" fill="none" stroke="var(--card-white)" stroke-width="1.2"/>
          <path d="M505 216.5 l5.5 4.5 l5.5 -4.5" fill="none" stroke="var(--card-white)" stroke-width="1.2"/>
        </g>
        <g class="icon icon-globe">
          <rect x="502" y="242" width="17" height="17" rx="2" fill="var(--ink)"/>
          <circle cx="510.5" cy="250.5" r="5" fill="none" stroke="var(--card-white)" stroke-width="1.2"/>
          <path d="M505.5 250.5 h10 M510.5 245.5 v10" stroke="var(--card-white)" stroke-width="1"/>
        </g>
      </g>
    </svg>
  </section>

</main>
</body>
</html>
```